Business Card for Professional Photographer

I'm looking for an eye catching modern clean design that compliments my logo/ website fonts & colours.
I specialise in architecture, corporate & commercial photography so I'm marketing to professional clients rather than portrait / wedding clients.

I would prefer to not have a solid black design.

My logo brand guide is as follows :

Main front font. : Reislust
Main font colour : #fff
Slogan front font : Ubuntu Bold
Monogram front font : Venti Medium
Container colour : #fff

I need print ready files in pdf .png & .eps formats.

Included in the files below are some screen grabs as reference to font & colours etc.

```html
<!DOCTYPE html>
<html lang="en">
<head>
<meta charset="utf-8">
<title>Lumen Axis – Business Card</title>
<link rel="stylesheet" href="https://fonts.googleapis.com/css2?family=Open+Sans:wght@300;400;700&display=swap">
<style>
  :root {
    --bg: #1d1d1f;
    --card: #2a2a2b;
    --gold: #d2a64e;
    --gold-light: #f0d38a;
    --white: #ffffff;
    --text-font: "Open Sans", sans-serif;
  }
  * { margin: 0; padding: 0; box-sizing: border-box; }
  html, body { width: 1200px; height: 913px; overflow: hidden; background: var(--bg); }
  .canvas { position: relative; width: 1200px; height: 913px; font-family: var(--text-font); }

  .card {
    position: absolute;
    width: 540px;
    height: 310px;
    background: var(--card);
    border-radius: 18px;
    overflow: hidden;
  }
  .card--front { left: 70px; top: 90px; }
  .card--back  { left: 590px; top: 510px; }

  /* Front */
  .brand { position: absolute; left: 70px; top: 110px; display: flex; align-items: center; gap: 28px; }
  .brand__mark {
    width: 90px; height: 90px; border-radius: 50%;
    border: 4px solid var(--gold);
  }
  .brand__name {
    font-weight: 300; font-size: 34px; letter-spacing: 8px;
    color: var(--white); line-height: 1;
  }
  .brand__tagline {
    margin-top: 10px; font-weight: 700; font-size: 10px;
    letter-spacing: 3px; color: var(--gold);
  }

  /* Back */
  .back__mark {
    position: absolute; right: 60px; top: 32px;
    width: 76px; height: 76px; border-radius: 50%;
    border: 4px solid var(--gold);
  }
  .person__name {
    position: absolute; left: 40px; top: 132px;
    font-weight: 700; font-size: 24px; color: var(--gold);
    letter-spacing: 0.5px; line-height: 1;
  }
  .person__role {
    position: absolute; left: 40px; top: 160px;
    color: var(--white); font-size: 16px; line-height: 1.2;
  }
  .back__rule {
    position: absolute; left: 40px; right: 40px; top: 190px; height: 1px;
    background: linear-gradient(90deg, var(--gold), var(--gold-light));
  }
  .contact {
    position: absolute; left: 40px; top: 202px; list-style: none;
  }
  .contact li {
    display: flex; align-items: center; gap: 8px;
    color: var(--white); font-size: 16px; line-height: 24px;
  }
  .contact svg { width: 13px; height: 13px; fill: var(--gold); flex: none; }
  .address {
    position: absolute; right: 40px; top: 202px; text-align: right;
    color: var(--white); font-size: 15px; line-height: 24px;
  }
</style>
</head>
<body>
<main class="canvas">

  <section class="card card--front" aria-label="Card front">
    <div class="brand">
      <span class="brand__mark"></span>
      <div>
        <div class="brand__name">LUMEN AXIS</div>
        <div class="brand__tagline">Architecture Corporate Commercial</div>
      </div>
    </div>
  </section>

  <section class="card card--back" aria-label="Card back">
    <span class="back__mark"></span>
    <div class="person__name">DANIEL ROARKE</div>
    <div class="person__role">Director</div>
    <div class="back__rule"></div>
    <ul class="contact">
      <li><svg viewBox="0 0 24 24"><path d="M6.6 10.8a15 15 0 0 0 6.6 6.6l2.2-2.2c.3-.3.7-.4 1-.2 1.1.4 2.3.6 3.6.6.6 0 1 .4 1 1V20c0 .6-.4 1-1 1A17 17 0 0 1 3 4c0-.6.4-1 1-1h3.5c.6 0 1 .4 1 1 0 1.3.2 2.5.6 3.6.1.3 0 .7-.2 1z"/></svg>555 214 0387</li>
      <li><svg viewBox="0 0 24 24"><path d="M2 5h20v14H2zm2 2v.5l8 5 8-5V7z"/></svg>info@lumenaxis.com</li>
      <li><svg viewBox="0 0 24 24"><circle cx="12" cy="12" r="10"/></svg>www.lumenaxis.com</li>
    </ul>
    <div class="address">148, Harbor Street<br>Portland OR 97204</div>
  </section>

</main>
</body>
</html>
```